Executive Business Card for Healthcare Company [Need Today]

I need a business card design for a healthcare company. The only branding the company has thus far is a logo. The cards will be utilized by company executives. The design I envision will be vibrant and appealing but with a corporate feel. They shouldn't be too casual or playful. I would like to complete this project TODAY if possible.

Target Market(s)

Healthcare vendors, other executives in healthcare and pharmaceuticals

Industry/Entity Type

Pharmaceutical

Contact Information for Business Card

See attachment

Font styles to use
Serif
Sans Serif

Colors

Designer to choose colors to be used in the design.

```html
<!DOCTYPE html>
<html lang="en">
<head>
<meta charset="utf-8">
<title>Corvan Therapeutics – Business Card</title>
<link rel="stylesheet" href="https://fonts.googleapis.com/css2?family=Arimo:wght@400;700&display=swap">
<style>
  :root {
    --canvas: #e9eaea;
    --card-white: #ffffff;
    --brand-green: #6cc49a;
    --brand-teal: #3bbfc9;
    --ink-white: #ffffff;
    --shadow: rgba(0, 0, 0, 0.12);
  }
  * { margin: 0; padding: 0; box-sizing: border-box; }
  html, body {
    width: 1200px; height: 900px; overflow: hidden;
    background: var(--canvas);
    font-family: "Arimo", Arial, sans-serif;
  }
  .stage { position: relative; width: 1200px; height: 900px; }

  .card {
    position: absolute;
    background: var(--card-white);
    box-shadow: 0 6px 18px var(--shadow);
    overflow: hidden;
  }

  /* Front */
  .card-front { left: 78px; top: 35px; width: 587px; height: 363px; }
  .card-front .field { position: absolute; inset: 0; }
  .brand-vertical {
    position: absolute;
    left: 34px; top: 150px;
    transform: translate(-50%, -50%) rotate(-90deg);
    font-size: 44px; font-weight: 400;
    color: var(--brand-teal);
    letter-spacing: 1px;
  }
  .details {
    position: absolute;
    right: 35px; top: 60px;
    text-align: right;
    color: var(--ink-white);
  }
  .person-name { font-size: 20px; font-weight: 700; letter-spacing: 0.3px; line-height: 26px; }
  .person-title { font-size: 16px; line-height: 20px; }
  .contact-list { list-style: none; margin-top: 90px; margin-right: -24px; }
  .contact-list li {
    display: flex; justify-content: flex-end; align-items: center;
    font-size: 16px; line-height: 21.5px;
  }
  .contact-list svg { width: 19px; height: 19px; margin-left: 4px; }
  .company { margin-top: 16px; }
  .company-name { font-size: 16px; font-weight: 700; line-height: 22px; }
  .company-address { font-size: 16px; line-height: 21px; font-style: normal; }

  /* Back */
  .card-back {
    left: 388px; top: 505px; width: 567px; height: 352px;
    display: flex; align-items: center; justify-content: center;
  }
  .brand-lockup { display: flex; align-items: center; gap: 18px; margin-left: 24px; }
  .brand-mark {
    width: 106px; height: 106px; border-radius: 50%;
    border: 4px solid var(--brand-green);
  }
  .brand-name {
    font-size: 40px; font-weight: 400; line-height: 1;
    color: var(--brand-teal);
  }
</style>
</head>
<body>
<main class="stage">

  <section class="card card-front" aria-label="Business card front">
    <svg class="field" viewBox="0 0 587 363" preserveAspectRatio="none" aria-hidden="true">
      <path d="M230 0 H587 V363 H0 V335 C70 300 190 270 240 210 C285 150 205 70 230 0 Z" fill="var(--brand-green)"/>
    </svg>

    <div class="brand-vertical">corvan</div>

    <div class="details">
      <h1 class="person-name">DANIEL MARSH</h1>
      <p class="person-title">Senior Director of Marketing</p>

      <ul class="contact-list">
        <li>555-014-2837
          <svg viewBox="0 0 20 20" aria-label="Office phone"><circle cx="10" cy="10" r="8.5" fill="none" stroke="#fff" stroke-width="1.3"/><path d="M5.5 9 Q10 5 14.5 9 L13 10.5 L11.5 9.5 H8.5 L7 10.5 Z M7 11 H13 V14 H7 Z" fill="#fff"/></svg>
        </li>
        <li>555-019-4462
          <svg viewBox="0 0 20 20" aria-label="Mobile phone"><circle cx="10" cy="10" r="8.5" fill="none" stroke="#fff" stroke-width="1.3"/><rect x="7.5" y="5" width="5" height="10" rx="1" fill="none" stroke="#fff" stroke-width="1.2"/></svg>
        </li>
        <li>dmarsh@corvanrx.com
          <svg viewBox="0 0 20 20" aria-label="Email"><circle cx="10" cy="10" r="8.5" fill="none" stroke="#fff" stroke-width="1.3"/><rect x="5.5" y="7" width="9" height="6.5" fill="#fff"/><path d="M5.5 7 L10 11 L14.5 7" fill="none" stroke="var(--brand-green)" stroke-width="1"/></svg>
        </li>
      </ul>

      <div class="company">
        <p class="company-name">CORVAN THERAPEUTICS, LLC</p>
        <address class="company-address">118 W Meridian Avenue<br>Dalton, GA 30720</address>
      </div>
    </div>
  </section>

  <section class="card card-back" aria-label="Business card back">
    <div class="brand-lockup">
      <span class="brand-mark" aria-hidden="true"></span>
      <span class="brand-name">corvan therapeutics</span>
    </div>
  </section>

</main>
</body>
</html>
```